Coastline Premier Retreats Business Card Design

Design a business card for Coastline Premier Retreats. Look at the website for colors and reference. Card should have logo, name, title, office number, mobile number, email, URL and a tagline like, "Luxury Hotel & Resort Email Marketing" (This might change).

https://www.coastlinepremierretreats.example

The rest I will leave up to your imagination.

Contact Information for Business Card

Logo, name, title, office number, mobile number, email, URL and a tagline like, "Luxury Hotel & Resort Email Marketing" (This might change).

```html
<!DOCTYPE html>
<html lang="en">
<head>
<meta charset="utf-8">
<title>Coastline Premier Retreats – Business Card</title>
<link rel="stylesheet" href="https://fonts.googleapis.com/css2?family=Poppins:wght@400;600;700&display=swap">
<style>
  :root {
    --stage: #3b3b3b;
    --card-black: #0d0d0d;
    --pattern-tone: #1a1a1a;
    --white: #ffffff;
    --ink: #111111;
    --orange: #f47a10;
    --divider: #9a9a9a;
  }
  * { box-sizing: border-box; margin: 0; padding: 0; }
  html, body {
    width: 1200px; height: 689px; overflow: hidden;
    background: var(--stage);
    font-family: "Poppins", sans-serif;
  }
  .stage { position: relative; width: 1200px; height: 689px; }
  .card {
    position: absolute; top: 196px;
    width: 520px; height: 297px;
    border-radius: 18px; overflow: hidden;
    box-shadow: 0 18px 40px rgba(0,0,0,.45);
  }

  /* Back side */
  .card-back { left: 50px; background: var(--card-black); }
  .back-pattern {
    position: absolute; inset: 0;
    background: linear-gradient(135deg, var(--pattern-tone), var(--card-black) 60%, var(--pattern-tone));
  }
  .back-content {
    position: absolute; inset: 0;
    display: flex; flex-direction: column; align-items: center; justify-content: center;
    gap: 14px;
  }
  .brand {
    display: flex; align-items: center; gap: 10px;
    font-weight: 700; text-transform: uppercase; letter-spacing: .5px;
  }
  .brand-square { width: 14px; height: 14px; background: var(--orange); flex: none; }
  .card-back .brand { color: var(--white); font-size: 17px; }
  .tagline {
    color: var(--white); font-weight: 600; font-size: 12.5px;
    letter-spacing: 1.6px; text-transform: uppercase;
  }

  /* Front side */
  .card-front { left: 630px; background: var(--white); }
  .front-main {
    position: absolute; left: 0; top: 0; right: 0; height: 222px;
    display: flex; align-items: center;
  }
  .front-brand { width: 230px; display: flex; justify-content: center; }
  .card-front .brand { color: var(--ink); font-size: 15px; }
  .divider { width: 1px; height: 80px; background: var(--divider); }
  .contact { padding-left: 26px; }
  .person-name { font-weight: 700; font-size: 18px; text-transform: uppercase; color: var(--ink); line-height: 1.1; }
  .person-title { color: var(--orange); font-size: 12px; margin-bottom: 10px; }
  .contact-list { list-style: none; }
  .contact-list li {
    display: flex; align-items: center; gap: 8px;
    font-size: 11px; color: var(--ink); line-height: 1.7;
  }
  .contact-list svg { width: 12px; height: 12px; flex: none; }
  .front-rule { position: absolute; left: 0; right: 0; top: 222px; height: 3px; background: var(--orange); }
  .front-band {
    position: absolute; left: 0; right: 0; top: 225px; bottom: 0;
    background: var(--card-black);
    display: flex; align-items: center; justify-content: center;
  }
  .website { color: var(--orange); font-size: 13px; letter-spacing: 1.2px; }
</style>
</head>
<body>
<main class="stage">

  <section class="card card-back">
    <div class="back-pattern" role="img" aria-label="Repeating embossed brand pattern on black"></div>
    <div class="back-content">
      <div class="brand"><span class="brand-square"></span>Coastline Premier Retreats</div>
      <p class="tagline">Luxury Hotel &amp; Resort Email Marketing</p>
    </div>
  </section>

  <section class="card card-front">
    <div class="front-main">
      <div class="front-brand">
        <div class="brand"><span class="brand-square"></span>Coastline Premier<br>Retreats</div>
      </div>
      <div class="divider"></div>
      <div class="contact">
        <h1 class="person-name">Daniel Reyes</h1>
        <p class="person-title">Managing Director</p>
        <ul class="contact-list">
          <li>
            <svg viewBox="0 0 24 24" aria-hidden="true"><path fill="#f47a10" d="M6.6 10.8a15.1 15.1 0 0 0 6.6 6.6l2.2-2.2a1 1 0 0 1 1-.25 11.4 11.4 0 0 0 3.6.57 1 1 0 0 1 1 1V20a1 1 0 0 1-1 1A17 17 0 0 1 3 4a1 1 0 0 1 1-1h3.5a1 1 0 0 1 1 1c0 1.25.2 2.45.57 3.57a1 1 0 0 1-.25 1z"/></svg>
            044-555 010 234
          </li>
          <li>
            <svg viewBox="0 0 24 24" aria-hidden="true"><rect x="6" y="2" width="12" height="20" rx="2" fill="none" stroke="#f47a10" stroke-width="2"/><circle cx="12" cy="18" r="1.2" fill="#f47a10"/></svg>
            044-555 010 567
          </li>
          <li>
            <svg viewBox="0 0 24 24" aria-hidden="true"><rect x="2" y="5" width="20" height="14" rx="1" fill="#f47a10"/><path d="M2 6l10 7 10-7" fill="none" stroke="#fff" stroke-width="1.6"/></svg>
            hello@coastlinepremierretreats.example
          </li>
        </ul>
      </div>
    </div>
    <div class="front-rule"></div>
    <div class="front-band">
      <p class="website">www.coastlinepremierretreats.example</p>
    </div>
  </section>

</main>
</body>
</html>
```